Manufacturers Catalog Cover Page

We are looking to have a cover to our catalog page designed. I currently have begun work for the remained of the catalog in InDesign and want the cover created in InDesign. I will provide photos.

Looking to beable to add the cover to our existing attached catalog.

Gathering more feedback

Industry/Entity Type

Manufacturing

Requirements
Must have
• Colors match what we are currently using. The Dark grey and gold
Nice to have
• modern, clean

```html
<!DOCTYPE html>
<html lang="en">
<head>
<meta charset="utf-8">
<title>Meridian Polymers – Catalog Cover</title>
<link href="https://fonts.googleapis.com/css2?family=Bebas+Neue&display=swap" rel="stylesheet">
<style>
  :root {
    --stage: #1e1e1f;
    --cover-dark: #3a3a3d;
    --band-grey: #6a6a6d;
    --gold: #c2b283;
    --white: #ffffff;
    --text-light: #e9e9ea;
  }
  html, body {
    margin: 0;
    padding: 0;
    width: 1200px;
    height: 1104px;
    overflow: hidden;
    background: var(--stage);
  }
  .catalog-cover {
    position: absolute;
    left: 220px;
    top: 60px;
    width: 760px;
    height: 984px;
    background: var(--cover-dark);
    overflow: hidden;
    font-family: "Bebas Neue", "Arial Narrow", sans-serif;
    color: var(--white);
  }
  .cover-art {
    position: absolute;
    inset: 0;
  }
  .brand {
    position: absolute;
    left: 452px;
    top: 84px;
    display: flex;
    align-items: center;
    gap: 16px;
  }
  .brand-dot {
    width: 58px;
    height: 58px;
    border-radius: 50%;
    background: var(--gold);
  }
  .brand-name {
    font-size: 34px;
    line-height: 0.95;
    letter-spacing: 1px;
    color: var(--white);
  }
  .title-block {
    position: absolute;
    left: 250px;
    top: 352px;
    width: 500px;
    text-align: center;
  }
  .title-kicker {
    font-size: 30px;
    letter-spacing: 1px;
    color: var(--text-light);
    line-height: 1;
  }
  .title-main {
    margin: 6px 0 0;
    font-size: 80px;
    font-weight: 400;
    line-height: 0.9;
    letter-spacing: 2px;
    color: var(--white);
  }
  .contact {
    position: absolute;
    right: 26px;
    top: 884px;
    text-align: right;
    font-size: 23px;
    line-height: 1.15;
    letter-spacing: 1px;
    color: var(--white);
  }
</style>
</head>
<body>
  <main class="catalog-cover">
    <svg class="cover-art" width="760" height="984" viewBox="0 0 760 984" xmlns="http://www.w3.org/2000/svg">
      <defs>
        <linearGradient id="fill-trim-strips" x1="0" y1="0" x2="1" y2="1">
          <stop offset="0" stop-color="#f1f1f2"/>
          <stop offset="0.55" stop-color="#c9a592"/>
          <stop offset="1" stop-color="#3a3030"/>
        </linearGradient>
        <linearGradient id="fill-black-seals" x1="0" y1="0" x2="1" y2="1">
          <stop offset="0" stop-color="#f3f3f4"/>
          <stop offset="0.6" stop-color="#6d6d70"/>
          <stop offset="1" stop-color="#e6e6e8"/>
        </linearGradient>
        <linearGradient id="fill-silicone-profiles" x1="0" y1="0" x2="1" y2="1">
          <stop offset="0" stop-color="#f4f2f1"/>
          <stop offset="0.55" stop-color="#b56a4e"/>
          <stop offset="1" stop-color="#ece8e6"/>
        </linearGradient>
        <linearGradient id="fill-refinery" x1="0" y1="0" x2="0" y2="1">
          <stop offset="0" stop-color="#8fb0cf"/>
          <stop offset="0.5" stop-color="#a9a7a0"/>
          <stop offset="1" stop-color="#5f7385"/>
        </linearGradient>
      </defs>

      <g class="gold-accents" fill="var(--gold)">
        <polygon points="0,110 122,232 0,355"/>
        <polygon points="0,245 185,430 0,615"/>
        <polygon points="0,505 185,690 0,875"/>
        <polygon points="0,765 195,960 0,960"/>
        <rect class="gold-footer-band" x="0" y="958" width="760" height="26"/>
      </g>

      <polygon class="title-band" fill="var(--band-grey)"
               points="310,340 760,340 760,520 305,520 217,432"/>

      <g class="product-tile">
        <polygon fill="var(--white)" points="200,175 325,300 200,425 75,300"/>
        <g role="img" aria-label="Photo of coiled rubber trim strips with adhesive backing">
          <polygon fill="url(#fill-trim-strips)" points="200,187 313,300 200,413 87,300"/>
        </g>
      </g>

      <g class="product-tile">
        <polygon fill="var(--white)" points="200,435 325,560 200,685 75,560"/>
        <g role="img" aria-label="Photo of black extruded rubber seal profiles">
          <polygon fill="url(#fill-black-seals)" points="200,447 313,560 200,673 87,560"/>
        </g>
      </g>

      <g class="product-tile">
        <polygon fill="var(--white)" points="200,695 325,820 200,945 75,820"/>
        <g role="img" aria-label="Photo of orange and white silicone gasket profiles">
          <polygon fill="url(#fill-silicone-profiles)" points="200,707 313,820 200,933 87,820"/>
        </g>
      </g>

      <g class="industry-tile" role="img" aria-label="Photo of an industrial refinery reflected in water">
        <polygon fill="url(#fill-refinery)" points="370,560 500,690 370,820 240,690"/>
      </g>
    </svg>

    <div class="brand">
      <span class="brand-dot"></span>
      <span class="brand-name">Meridian<br>Polymers</span>
    </div>

    <div class="title-block">
      <div class="title-kicker">Rubber &amp; Plastic Extusion</div>
      <h1 class="title-main">Gaskets<br>Trims &amp; Seals</h1>
    </div>

    <div class="contact">
      <div class="contact-phones">888-555-0142 &nbsp;|&nbsp; 330-555-0187</div>
      <div class="contact-web">www.meridianpolymers.com</div>
    </div>
  </main>
</body>
</html>
```